RW Framewell Inc Business cards

We need business cards using our existing logo but slightly modified. Right now the logo says RW Loadbearing Masonry. We want to keep the RW part of the design, but replace the Structural Concrete portion with "FRAMEWELL". Please see the attached file.
Ideally this would be a blank template so we can add Different Names, titles, and phone numbers later.
On the one side we want only the logo and on the other side the detail. I'm attaching an example for you to see.
Please reach out with any other questions. Our address and other details will be given out once we find a design we like.

Target Market(s)

Construction Industry

```html
<!DOCTYPE html>
<html lang="en">
<head>
<meta charset="utf-8">
<title>RW Framewell Inc – Business Cards</title>
<link rel="stylesheet" href="https://fonts.googleapis.com/css2?family=Montserrat:wght@600;700&family=Roboto:wght@400;500;700&display=swap">
<style>
  :root {
    --backdrop: #3b3b3c;
    --card: #1f1f21;
    --card-edge: #2a2a2d;
    --brand-blue: #2f66b0;
    --text-light: #f2f2f2;
    --emboss: #8d8d90;
  }
  * { box-sizing: border-box; margin: 0; padding: 0; }
  html, body {
    width: 799px; height: 1200px; overflow: hidden;
    background: var(--backdrop);
  }
  .sheet {
    position: relative; width: 799px; height: 1200px;
    display: flex; flex-direction: column; align-items: center;
    justify-content: space-around; padding: 60px 0;
  }
  .card {
    position: relative; width: 620px; height: 354px;
    background: var(--card);
    border: 1px solid var(--card-edge);
    box-shadow: 0 14px 30px rgba(0,0,0,.45);
    overflow: hidden;
  }
  /* Front: logo only */
  .card--front { display: flex; align-items: center; justify-content: center; }
  .brand-name {
    font-family: "Montserrat", sans-serif; font-weight: 700;
    letter-spacing: 6px; white-space: nowrap;
  }
  .card--front .brand-name { font-size: 46px; color: var(--emboss); }

  /* Back: details */
  .holder { position: absolute; left: 40px; top: 40px; }
  .holder__name {
    font-family: "Montserrat", sans-serif; font-weight: 700;
    font-size: 22px; color: var(--brand-blue);
  }
  .holder__title {
    font-family: "Roboto", sans-serif; font-size: 14px;
    color: var(--text-light); margin-top: 4px;
  }
  .contact {
    position: absolute; left: 40px; top: 170px;
    font-family: "Roboto", sans-serif; font-size: 15px;
    color: var(--text-light); line-height: 1.5; list-style: none;
  }
  .contact__item { display: flex; align-items: center; gap: 12px; }
  .contact__icon { width: 14px; height: 14px; flex: none; }
  .contact__address { margin-top: 2px; }
  .card--back .brand-name {
    position: absolute; right: 44px; top: 118px;
    font-size: 34px; color: var(--brand-blue);
  }
  .web-band {
    position: absolute; right: 0; bottom: 0; width: 360px; height: 74px;
    background: var(--brand-blue);
    border-top-left-radius: 34px;
    display: flex; align-items: center; justify-content: center;
  }
  .web-band__url {
    font-family: "Roboto", sans-serif; font-weight: 700;
    font-size: 18px; color: #fff; padding-top: 14px;
  }
</style>
</head>
<body>
<main class="sheet">
  <section class="card card--front" aria-label="Card front">
    <span class="brand-name">RW FRAMEWELL</span>
  </section>

  <section class="card card--back" aria-label="Card back">
    <div class="holder">
      <p class="holder__name">Mark RW Ellison</p>
      <p class="holder__title">Managing Director</p>
    </div>

    <ul class="contact">
      <li class="contact__item">
        <svg class="contact__icon" viewBox="0 0 16 16" aria-hidden="true">
          <path fill="#2f66b0" d="M3 1h3l1.5 4-2 1.3a9 9 0 0 0 4.2 4.2L11 8.5l4 1.5v3a2 2 0 0 1-2 2A12 12 0 0 1 1 3a2 2 0 0 1 2-2z"/>
        </svg>
        <span>828-555-0142</span>
      </li>
      <li class="contact__item">
        <svg class="contact__icon" viewBox="0 0 16 16" aria-hidden="true">
          <rect x="1" y="3" width="14" height="10" rx="1" fill="#2f66b0"/>
          <path d="M1.5 3.8 8 9l6.5-5.2" fill="none" stroke="#1f1f21" stroke-width="1.4"/>
        </svg>
        <span>mark@rwframewell.com</span>
      </li>
      <li class="contact__address">418 Beamline Rd., Ridgeford,<br>California, US 902145</li>
    </ul>

    <span class="brand-name">RW FRAMEWELL</span>

    <div class="web-band">
      <span class="web-band__url">www.rwframewell.com</span>
    </div>
  </section>
</main>
</body>
</html>
```